Corvel Capital LLC

Need Professional Business cards for New Investment Fund

Target Market(s)

High Quality investors

Industry/Entity Type

Financial

Contact Information for Business Card

Phone Number +1 555 284 6190
Name Lukas Varenko
Title Fund Manager
email lv@FundQuendrix.com
Website www.FundQuendrix.com

Colors

Designer to choose colors to be used in the design.

Requirements
Must have
• Must have our Logo and all of the above. Must be made so lettering and loge can be raised

```html
<!DOCTYPE html>
<html lang="en">
<head>
<meta charset="utf-8">
<title>Quendrix Capital – Business Card</title>
<link rel="stylesheet" href="https://fonts.googleapis.com/css2?family=Archivo+Narrow:wght@500;600;700&display=swap">
<style>
  :root {
    --backdrop: #68696b;
    --card-black: #151515;
    --accent-green: #7ee233;
    --paper-white: #f7f7f7;
    --ink-dark: #3f4a3b;
    --mark-grey: #5e5e5e;
    --arc-black: #000000;
  }
  * { margin: 0; padding: 0; box-sizing: border-box; }
  html, body { width: 1200px; height: 1200px; overflow: hidden; }
  body {
    background: var(--backdrop);
    position: relative;
    font-family: "Archivo Narrow", "Arial Narrow", sans-serif;
  }
  .card {
    position: absolute;
    left: 250px;
    width: 700px;
    height: 400px;
    overflow: hidden;
  }
  .card--front {
    top: 147px;
    background: var(--card-black);
    border-bottom: 6px solid var(--accent-green);
  }
  .card--back { top: 652px; }
  .card__shapes { position: absolute; inset: 0; }
  .brand {
    position: absolute;
    display: flex;
    align-items: center;
    gap: 12px;
    font-weight: 600;
    letter-spacing: 2px;
    text-transform: uppercase;
    white-space: nowrap;
  }
  .brand__square { display: block; }
  .card--front .brand {
    left: 350px;
    top: 188px;
    transform: translate(-50%, -50%);
    color: var(--mark-grey);
    font-size: 42px;
  }
  .card--front .brand__square {
    width: 30px; height: 30px;
    background: var(--mark-grey);
  }
  .card--back .brand {
    left: 165px;
    top: 212px;
    transform: translate(-50%, -50%);
    color: var(--ink-dark);
    font-size: 42px;
  }
  .card--back .brand__square {
    width: 30px; height: 30px;
    background: var(--accent-green);
  }
  .holder {
    position: absolute;
    left: 418px;
    top: 75px;
    color: var(--ink-dark);
  }
  .holder__name {
    font-size: 26px;
    font-weight: 700;
    letter-spacing: 3.2px;
    text-transform: uppercase;
    line-height: 1;
  }
  .holder__title {
    margin-top: 14px;
    font-size: 19px;
    font-weight: 600;
    letter-spacing: 1.6px;
    line-height: 1;
  }
  .contact {
    position: absolute;
    left: 418px;
    top: 273px;
    list-style: none;
    color: var(--ink-dark);
    font-size: 19px;
    font-weight: 600;
    letter-spacing: 2.2px;
    line-height: 26.5px;
    white-space: nowrap;
  }
</style>
</head>
<body>
  <section class="card card--front" aria-label="Card front">
    <div class="brand">
      <span class="brand__square"></span>
      <span class="brand__name">Quendrix</span>
    </div>
  </section>

  <section class="card card--back" aria-label="Card back">
    <svg class="card__shapes" width="700" height="400" viewBox="0 0 700 400" aria-hidden="true">
      <rect width="700" height="400" fill="var(--accent-green)"/>
      <circle cx="103" cy="200" r="276" fill="var(--arc-black)"/>
      <circle cx="54" cy="200" r="280" fill="var(--paper-white)"/>
    </svg>
    <div class="brand">
      <span class="brand__square"></span>
      <span class="brand__name">Quendrix</span>
    </div>
    <div class="holder">
      <p class="holder__name">Lukas Varenko</p>
      <p class="holder__title">Fund Manager</p>
    </div>
    <ul class="contact">
      <li>T: +1 555 284 6190</li>
      <li>E: lv@FundQuendrix.com</li>
      <li>W: www.FundQuendrix.com</li>
    </ul>
  </section>
</body>
</html>
```